Brindlewick Solutions Ltd

I'd like to create a company letterhead for the attached logo in word format.

I'd like to emphasis the icon in large translucent state from the left corner and ensure that the letterhead colouring matches the colour palette of the current logo with a contrast so it's clear to see. I've attached a copy of our sister company page on the app for reference.

```html
<!DOCTYPE html>
<html lang="en">
<head>
<meta charset="utf-8">
<title>Brindlewick Solutions Ltd — Letterhead</title>
<link href="https://fonts.googleapis.com/css2?family=Lato:wght@400;700&display=swap" rel="stylesheet">
<style>
  :root {
    --backdrop: #e9e9e9;
    --paper: #ffffff;
    --ink: #2b2b2b;
    --ink-strong: #1a1a1a;
    --tab: #111111;
    --haze: #eeeeee;
    --haze-soft: #f7f7f7;
  }
  * { margin: 0; padding: 0; box-sizing: border-box; }
  html, body {
    width: 1061px; height: 1200px; overflow: hidden;
    background: var(--backdrop);
    font-family: "Lato", Arial, sans-serif;
    color: var(--ink);
  }
  .letterhead {
    position: absolute; left: 106px; top: 0;
    width: 848px; height: 1200px;
    background: var(--paper);
    overflow: hidden;
  }
  .brand {
    position: absolute; left: 63px; top: 72px;
    width: 220px; text-align: center;
  }
  .brand-dot {
    display: block; width: 64px; height: 64px; margin: 0 auto 12px;
    border-radius: 50%; background: var(--ink);
  }
  .brand-name {
    font-size: 33px; font-weight: 400; line-height: 1; color: var(--ink);
  }
  .brand-sub {
    margin-top: 6px; font-size: 10.5px; font-weight: 400;
    letter-spacing: 0.42em; color: var(--ink);
  }
  .contact {
    position: absolute; right: 64px; top: 70px;
    text-align: right; font-size: 13px; line-height: 19px; color: var(--ink);
  }
  .contact .company { font-weight: 700; color: var(--ink-strong); }
  .contact .channels { margin-top: 12px; }
  .contact .channel { display: flex; justify-content: flex-end; align-items: center; gap: 8px; }
  .contact .channel svg { width: 14px; height: 12px; fill: var(--ink-strong); }
  .contact .web { margin-top: 10px; font-weight: 700; color: var(--ink-strong); }
  .edge-tab {
    position: absolute; right: 0; top: 72px;
    width: 20px; height: 145px; background: var(--tab);
  }
  .backdrop-art {
    position: absolute; left: 0; top: 425px;
    width: 848px; height: 775px;
    background:
      radial-gradient(circle at 16% 78%, var(--haze) 0 170px, transparent 172px),
      radial-gradient(ellipse at 10% 100%, var(--haze) 0%, var(--haze-soft) 45%, var(--paper) 80%);
  }
</style>
</head>
<body>
  <main class="letterhead">
    <div class="backdrop-art" role="img" aria-label="Faint grey sunburst rays radiating from the lower left corner behind a large translucent brand circle"></div>

    <div class="brand">
      <span class="brand-dot"></span>
      <div class="brand-name">Brindlewick</div>
      <div class="brand-sub">SOLUTIONS LTD</div>
    </div>

    <address class="contact" style="font-style:normal">
      <div class="company">Brindlewick Solutions Ltd</div>
      <div>418 Alder Crest Lane</div>
      <div>Fairhaven, CT 06512</div>
      <div class="channels">
        <div class="channel">(203) 555-0148
          <svg viewBox="0 0 24 24" aria-label="Phone"><path d="M6.6 10.8a15.1 15.1 0 0 0 6.6 6.6l2.2-2.2c.3-.3.7-.4 1-.2 1.1.4 2.3.6 3.6.6.6 0 1 .4 1 1V20c0 .6-.4 1-1 1A17 17 0 0 1 3 4c0-.6.4-1 1-1h3.5c.6 0 1 .4 1 1 0 1.3.2 2.5.6 3.6.1.3 0 .7-.2 1z"/></svg>
        </div>
        <div class="channel">(203) 555-0149
          <svg viewBox="0 0 24 24" aria-label="Fax"><path d="M6 2h12v6H6zM3 9h18a1 1 0 0 1 1 1v7h-4v5H6v-5H2v-7a1 1 0 0 1 1-1zm5 8v3h8v-3z"/></svg>
        </div>
        <div class="channel">info@brindlewicksolutions.com
          <svg viewBox="0 0 24 24" aria-label="Email"><path d="M2 5h20v2l-10 6L2 7zm0 4.3 10 6 10-6V19H2z"/></svg>
        </div>
      </div>
      <div class="web">brindlewicksolutions.com</div>
    </address>

    <div class="edge-tab"></div>
  </main>
</body>
</html>
```